Design a web site for my business - Brightline Coatings Co.

We are a family business that handles design, fabrication and installation of powder coated aluminum, stainless steel and glass products. Including handrails, privacy slat screens, electric gates and pool fencing. We are based in the Whitsundays in North Queensland and service an area from Airlie Beach to Townsville.

Target Market(s)

Domestic and commercial

Industry/Entity Type

fabrication - manufacturing

Coding

Coded - Design and coding required

Number of Pages Required

5+ page

Colors
0054AA
0677BA
7BADD7
CADEEF
E8F1F8

Requirements
Must have
• photo galleries, contact page, one page for privacy screens, balustrades, glass fencing, stainless steel handrail, powder coated aluminium handrails and pool fencing

```html
<!DOCTYPE html>
<html lang="en">
<head>
<meta charset="UTF-8">
<title>Projects — Brightline Coatings Co</title>
<link rel="stylesheet" href="https://fonts.googleapis.com/css2?family=Inter:wght@400;500;600;700&family=Montserrat:wght@500;600;700&display=swap">
<style>
:root{
  --ink:#15191c;
  --ink-soft:#3d454b;
  --blue:#0054AA;
  --blue-mid:#0677BA;
  --blue-light:#7BADD7;
  --blue-pale:#CADEEF;
  --bg:#F3F8FC;
  --band:#EAF2F7;
  --pill:#E4EBF0;
  --footer:#1a1f22;
  --footer-text:#8d969c;
}
*{box-sizing:border-box;margin:0;padding:0}
html,body{width:1200px;height:3343px;overflow:hidden}
body{background:var(--bg);font-family:"Inter",sans-serif;color:var(--ink);position:relative}
.site-header{position:absolute;top:0;left:0;width:1200px;height:75px;border-bottom:1px solid #e3eaef;background:var(--bg);display:flex;align-items:center;padding:0 62px;justify-content:space-between}
.brand{font-family:"Montserrat",sans-serif;font-weight:600;font-size:22px;letter-spacing:-0.5px;text-transform:uppercase}
.main-nav{display:flex;align-items:center;gap:30px;font-size:14px;font-weight:500;color:var(--ink-soft)}
.main-nav a{color:inherit;text-decoration:none}
.main-nav .active{color:var(--blue);font-weight:600;border-bottom:2px solid var(--blue);padding-bottom:4px}
.btn{display:inline-flex;align-items:center;justify-content:center;font-family:"Inter",sans-serif;font-weight:600;font-size:14px;border-radius:6px;text-decoration:none}
.btn-dark{background:var(--ink);color:#fff}
.btn-outline{border:2px solid var(--ink);color:var(--ink);background:#fff}
.nav-cta{width:152px;height:33px;font-size:13px;margin-left:4px}
.glow{position:absolute;right:-40px;top:60px;width:320px;height:260px;border-radius:50%;background:radial-gradient(circle,#e6eef4 0%,rgba(230,238,244,0) 70%)}
.hero{position:absolute;left:62px;top:148px;width:760px}
.eyebrow{font-size:13px;font-weight:600;letter-spacing:1.6px;color:var(--blue);text-transform:uppercase}
.hero h1{font-family:"Montserrat",sans-serif;font-weight:700;font-size:62px;line-height:65px;letter-spacing:-1.5px;margin-top:18px}
.hero p{font-size:17px;line-height:27.5px;color:var(--ink-soft);margin-top:26px;width:730px}
.filters{position:absolute;left:62px;top:490px;width:1076px;height:63px;border-bottom:1px solid #dfe6eb;display:flex;align-items:flex-start;gap:16px}
.filters .label{font-size:13px;font-weight:500;letter-spacing:1px;color:var(--ink-soft);line-height:32px;margin-right:16px}
.pill{height:32px;padding:0 22px;border-radius:16px;background:var(--pill);font-size:13.5px;font-weight:600;display:flex;align-items:center;color:var(--ink)}
.pill.on{background:var(--ink);color:#fff}
.card{position:absolute;border-radius:10px;overflow:hidden}
.card .photo{position:absolute;inset:0}
.card .shade{position:absolute;inset:0;background:linear-gradient(to top,rgba(10,16,22,.78) 0%,rgba(10,16,22,.25) 38%,rgba(10,16,22,0) 60%)}
.card .info{position:absolute;left:30px;right:30px;bottom:22px;color:#fff}
.tags{display:flex;gap:8px;margin-bottom:10px}
.tag{font-size:9.5px;font-weight:700;letter-spacing:1px;padding:5px 11px;border-radius:12px;text-transform:uppercase}
.tag.loc{background:var(--blue)}
.tag.type{background:rgba(255,255,255,.22)}
.card h2{font-family:"Montserrat",sans-serif;font-weight:600;font-size:30px;line-height:34px}
.card.slim h2{font-size:23px;line-height:32px}
.card p{font-size:14.5px;line-height:23px;color:rgba(255,255,255,.88);margin-top:10px}
.values{position:absolute;left:0;top:2162px;width:1200px;height:232px;background:var(--band);display:flex;padding:0 62px;align-items:center}
.value{display:flex;gap:22px;align-items:flex-start}
.value .icon{width:42px;height:58px;border-radius:21px;display:flex;align-items:center;justify-content:center;flex:none;margin-top:6px}
.value h3{font-family:"Montserrat",sans-serif;font-weight:600;font-size:24px}
.value p{font-size:15px;line-height:23px;color:var(--ink-soft);margin-top:4px}
.cta{position:absolute;left:0;top:2508px;width:1200px;text-align:center}
.cta h2{font-family:"Montserrat",sans-serif;font-weight:700;font-size:47px;line-height:55px;letter-spacing:-0.5px}
.cta p{font-size:17px;line-height:27.5px;color:var(--ink-soft);margin:36px auto 0;width:620px}
.cta .actions{display:flex;justify-content:center;gap:15px;margin-top:44px}
.cta .btn{height:49px;font-size:13.5px;letter-spacing:.3px}
.site-footer{position:absolute;left:0;top:2918px;width:1200px;height:425px;background:var(--footer);color:var(--footer-text)}
.footer-about{position:absolute;left:62px;top:174px;width:250px;font-size:15px;line-height:24px}
.footer-col{position:absolute;top:78px}
.footer-col h4{font-size:13px;font-weight:600;letter-spacing:1.6px;color:#fff;margin-bottom:22px}
.footer-col li{list-style:none;font-size:11.5px;line-height:37.6px}
.social{display:flex;gap:14px}
.social span{width:36px;height:36px;border-radius:50%;background:#2c3338;display:flex;align-items:center;justify-content:center}
.privacy{font-size:11.5px;margin-top:24px}
.footer-base{position:absolute;left:0;bottom:0;width:1200px;height:59px;border-top:1px solid #2c3338;text-align:center;font-size:11px;line-height:56px}
</style>
</head>
<body>
<header class="site-header">
  <div class="brand">Brightline Coatings Co</div>
  <nav class="main-nav">
    <a href="#">Home</a><a href="#">Products</a><a href="#">Process</a><a href="#" class="active">Projects</a>
    <a href="#" class="btn btn-dark nav-cta">Request a Quote</a>
  </nav>
</header>
<div class="glow"></div>

<section class="hero">
  <div class="eyebrow">Craftsmanship in metal &amp; glass</div>
  <h1>Past Projects &amp;<br>Portfolio</h1>
  <p>Explore our gallery of completed residential and commercial works. From the luxury waterfronts of Airlie Beach to industrial builds in Townsville, we deliver structural integrity with architectural elegance.</p>
</section>

<div class="filters">
  <span class="label">FILTER BY:</span>
  <span class="pill on">All Projects</span>
  <span class="pill">Residential</span>
  <span class="pill">Commercial</span>
  <span class="pill">Glass &amp; Pool</span>
  <span class="pill">Gates &amp; Fencing</span>
</div>

<article class="card" style="left:62px;top:598px;width:710px;height:467px">
  <div class="photo" role="img" aria-label="Oceanfront villa with infinity pool and frameless glass balustrades overlooking the sea" style="background:linear-gradient(160deg,#7fb2e0 0%,#b9d6ea 30%,#2fa6c4 55%,#5cc2cf 75%,#9aa6a8 100%)"></div>
  <div class="shade"></div>
  <div class="info">
    <div class="tags"><span class="tag loc">Airlie Beach</span><span class="tag type">Residential</span></div>
    <h2>Oceanfront Glass Balustrades</h2>
    <p>Frameless architectural glass designed to withstand cyclonic conditions<br>while providing 100% visibility of the Coral Sea.</p>
  </div>
</article>

<article class="card slim" style="left:794px;top:598px;width:344px;height:467px">
  <div class="photo" role="img" aria-label="Commercial storefront clad in dark slat screens with lit entrance" style="background:linear-gradient(170deg,#6e86a6 0%,#4a4440 35%,#3a2e26 60%,#6a5640 80%,#5b5d60 100%)"></div>
  <div class="shade"></div>
  <div class="info">
    <div class="tags"><span class="tag loc">Townsville</span></div>
    <h2>Commercial Security Shell</h2>
    <p>Precision slat screens for privacy and high-traffic security gates.</p>
  </div>
</article>

<article class="card slim" style="left:62px;top:1087px;width:344px;height:560px">
  <div class="photo" role="img" aria-label="Bright interior staircase with timber treads and black metal handrail" style="background:linear-gradient(160deg,#f2f2f0 0%,#dedbd6 40%,#b08a64 70%,#6d5f52 100%)"></div>
  <div class="shade"></div>
  <div class="info">
    <div class="tags"><span class="tag type">Proserpine</span></div>
    <h2>Modern Interior Metalwork</h2>
    <p>Sleek, minimalist handrails integrated with native hardwood stairs.</p>
  </div>
</article>

<article class="card" style="left:428px;top:1087px;width:710px;height:560px">
  <div class="photo" role="img" aria-label="Tropical estate with pool, palms and patterned black privacy screens" style="background:linear-gradient(175deg,#a8cbe6 0%,#d8e6ee 22%,#6f8a66 45%,#3f8fa0 60%,#3d4a3a 80%,#4f6a3a 100%)"></div>
  <div class="shade"></div>
  <div class="info">
    <div class="tags"><span class="tag loc">Whitsundays</span></div>
    <h2>Estate Perimeter &amp; Privacy</h2>
    <p>Custom-patterned privacy screens and automated gate systems for a premium private residence.</p>
  </div>
</article>

<div class="card" style="left:62px;top:1670px;width:527px;height:373px" role="img" aria-label="Stainless steel wire balustrade on a timber deck overlooking a bay with yachts">
  <div class="photo" style="background:linear-gradient(170deg,#5f9ad6 0%,#a7c9e8 25%,#2c9fc0 50%,#3f8c8a 70%,#8a6a4c 100%)"></div>
</div>
<div class="card" style="left:611px;top:1670px;width:527px;height:373px" role="img" aria-label="Modern home entry with tall black aluminium slat gate casting shadows">
  <div class="photo" style="background:linear-gradient(165deg,#c9def0 0%,#e9edf0 30%,#6f7b6c 55%,#2a2e31 70%,#bcbab4 100%)"></div>
</div>

<section class="values">
  <div class="value" style="width:370px">
    <span class="icon" style="background:var(--ink)"><svg width="26" height="26" viewBox="0 0 24 24" fill="none" stroke="#fff" stroke-width="2"><path d="M12 2l2.4 2 3.1-.3.8 3 2.7 1.6-1.2 2.9 1.2 2.9-2.7 1.6-.8 3-3.1-.3L12 22l-2.4-2-3.1.3-.8-3L3 15.7l1.2-2.9L3 9.9l2.7-1.6.8-3 3.1.3z"/><path d="M8.5 12l2.4 2.4 4.6-4.6"/></svg></span>
    <div><h3>Australian Made</h3><p>Locally fabricated with high-grade Australian steel.</p></div>
  </div>
  <div class="value" style="width:390px">
    <span class="icon" style="background:var(--blue)"><svg width="24" height="26" viewBox="0 0 24 24" fill="none" stroke="#fff" stroke-width="2"><path d="M12 3l7 3v6c0 4.5-3 7.5-7 9-4-1.5-7-4.5-7-9V6z"/></svg></span>
    <div><h3>Cyclone Rated</h3><p>Engineered to withstand the toughest tropical conditions.</p></div>
  </div>
  <div class="value" style="width:320px">
    <span class="icon" style="background:var(--ink)"><svg width="26" height="26" viewBox="0 0 24 24" fill="none" stroke="#fff" stroke-width="2"><rect x="3" y="3" width="6" height="6" rx="1"/><rect x="15" y="3" width="6" height="6" rx="1"/><circle cx="12" cy="18" r="3"/><path d="M6 9v3h12V9M12 12v3"/></svg></span>
    <div><h3>Family Business</h3><p>Serving the Whitsunday community for over 15 years.</p></div>
  </div>
</section>

<section class="cta">
  <h2>Ready to Start Your<br>Project?</h2>
  <p>Whether it's a coastal balcony, a secure commercial gate, or custom interior metalwork, we bring your vision to life with precision.</p>
  <div class="actions">
    <a href="#" class="btn btn-dark" style="width:218px">Get a Detailed Quote</a>
    <a href="#" class="btn btn-outline" style="width:231px">View Technical Specs</a>
  </div>
</section>

<footer class="site-footer">
  <p class="footer-about">Premium metal and glass solutions for luxury residential and commercial properties across North Queensland.</p>
  <div class="footer-col" style="left:336px">
    <h4>SERVICES</h4>
    <ul><li>Handrails</li><li>Slat Screens</li><li>Electric Gates</li><li>Pool Fencing</li></ul>
  </div>
  <div class="footer-col" style="left:611px">
    <h4>SERVICE AREAS</h4>
    <ul><li>Airlie Beach</li><li>Townsville</li><li>Proserpine</li><li>Bowen</li></ul>
  </div>
  <div class="footer-col" style="left:886px">
    <h4>CONNECT</h4>
    <div class="social">
      <span><svg width="18" height="18" viewBox="0 0 24 24" fill="none" stroke="#fff" stroke-width="2"><circle cx="12" cy="12" r="9"/><path d="M3 12h18M12 3c3 3 3 15 0 18"/></svg></span>
      <span><svg width="18" height="18" viewBox="0 0 24 24" fill="none" stroke="#fff" stroke-width="2"><rect x="3" y="6" width="18" height="14" rx="2"/><circle cx="12" cy="13" r="3.5"/><path d="M8 6l2-3h4l2 3"/></svg></span>
    </div>
    <p class="privacy">Privacy Policy</p>
  </div>
  <div class="footer-base">© 2024 Brightline Coatings Co. All Rights Reserved. Australian Made.</div>
</footer>
</body>
</html>
```